Mortgage Protection Insurance Flyer

The target audience are new home owners so the design needs to be clean and simple.

This a primarily for Final Expense Insurance, but need an area where it says "We Also Specialize In:"
- Medicare Supplement Insurance (MediGap)
- Annuities
- Final Expense

All flyer versions need to be editable. Colors to be used are red, white or black. Refer to my website for colors and photos (corvantshield.com). Will attach my logo and a flyer that I found online that is the format that I am looking for (for 8.5 in. x 11 in version). Need flyer in standard letter size 8.5 in. x11 in. but also in 8.5 in. x 5.5 in and 5.0 in. x 8.0 in. All sizes to be portrait oriented. If picked as winning design, need all flyer versions in full color, also in grey scale and files in all industry file types.

Content can be taken from my website..... corvantshield.com

Do NOT submit if you are not willing to provide all versions as described above for the original project price.

Must use royalty-free stock photos please.

Target Market(s)

New homeowners looking for insurance to protect there mortgage payments

Industry/Entity Type

Life Insurance

Colors
f69fa3

Requirements
Must have
• Colors to be used are red, white or black.
• Need flyer in standard letter size 8.5 in. x11 in. but also in 3.5 in. x 8.5 in (Full Bleed 3.75 in by 8.75 in.) and 4.0 in. x 6.0 in. (Full Bleed 4.12 in x 6.12 in) Each design tailored to the size dimensions (So no squeezing 8.5 x 11 design into a 4.0 x 6.0 space.) All sizes to be portrait oriented. If picked as winning design, need all flyer versions in full color, also in grey scale and files in all file types.
• Do not need physical address on flyer, do need email address on flyer though - tkelwer@corvantshield.com
• So phone number should be prominent, email address and website address should also be contact area.
• If you can not agree to terms above, do not submit any designs.
• Need facebook & twitter logos somewhere in contact info area.
Nice to have
• See sample flyers I have attached.
• White background with red used as primary graphic color and black used as secondary graphic if needed.
• font to be used should similar to one used in logo.

```html
<!DOCTYPE html>
<html lang="en">
<head>
<meta charset="utf-8">
<title>Corvant Shield – Insurance Flyer</title>
<link href="https://fonts.googleapis.com/css2?family=Exo+2:ital,wght@0,700;0,800;1,900&family=Montserrat:wght@400;500;600;700&display=swap" rel="stylesheet">
<style>
:root{
  --red:#e0242b;
  --black:#1d1d1f;
  --ink:#2b2b2d;
  --grey-cell:#4a4a4c;
  --paper:#f4f4f4;
  --stage:#3a3a3a;
  --photo-a:#dcdcdc;
  --photo-b:#b9b6b2;
}
*{box-sizing:border-box;margin:0;padding:0}
html,body{width:1200px;height:857px;overflow:hidden}
body{background:var(--stage);font-family:"Montserrat",sans-serif;color:var(--ink)}
.flyer{position:absolute;left:295px;top:18px;width:610px;height:820px;background:var(--paper);overflow:hidden}
.brand{position:absolute;left:32px;top:34px;display:flex;align-items:center;gap:8px}
.brand-mark{width:14px;height:14px;background:var(--red)}
.brand-name{font-family:"Exo 2",sans-serif;font-weight:800;font-size:30px;letter-spacing:.5px;color:var(--black);text-transform:uppercase;line-height:1}
.headline{position:absolute;left:31px;top:108px;font-family:"Exo 2",sans-serif;font-style:italic;font-weight:900;font-size:22px;line-height:25px;color:var(--red);text-transform:uppercase}
.intro{position:absolute;left:31px;top:164px;width:240px;font-size:12px;line-height:15px;font-weight:500;color:var(--black)}
.hero-photo{position:absolute;left:300px;top:0;width:310px;height:320px;background:radial-gradient(ellipse at 55% 45%,var(--photo-b),var(--photo-a) 70%,#ececec)}
.wave{position:absolute;left:0;width:610px}
.wave-top{top:240px;height:100px}
.wave-bottom{top:690px;height:130px}
.col{position:absolute;font-size:9.6px;line-height:12.4px}
.col-left{left:31px;top:298px;width:265px}
.col-right{left:322px;top:338px;width:256px}
.section-title{font-weight:700;font-size:12px;color:var(--red);margin-bottom:4px}
.about-title{font-family:"Exo 2",sans-serif;font-weight:800;font-size:15px;color:var(--red);text-transform:uppercase;margin-bottom:3px}
.sub-title{font-weight:700;font-size:12px;color:var(--black);margin-bottom:3px}
.also-title{font-weight:700;color:var(--black)}
.justify{text-align:justify}
.checks{list-style:none;margin:6px 0}
.checks li{position:relative;padding-left:13px;margin-bottom:6px}
.checks li::before{content:"";position:absolute;left:0;top:2px;width:7px;height:7px;border:1.2px solid var(--red);border-radius:1px}
.checks li::after{content:"";position:absolute;left:2px;top:2px;width:3px;height:5px;border-right:1.5px solid var(--red);border-bottom:1.5px solid var(--red);transform:rotate(40deg)}
.col-right .checks li{margin-bottom:5px}
.col-right .checks{margin:6px 0 8px}
.block{margin-bottom:13px}
.price-table{margin-top:23px;width:265px;border-collapse:separate;border-spacing:2px 3px;margin-left:-2px}
.price-table th{background:var(--grey-cell);color:#fff;font-weight:500;text-align:left;padding:3px 10px;font-size:9.8px}
.price-table td{background:var(--red);color:#fff;font-weight:700;text-align:center;width:90px;font-size:10px}
.disclaimer{margin-top:17px;font-size:9.8px;line-height:12.4px;font-weight:500;color:var(--black);text-align:justify}
.cta{position:absolute;left:31px;top:736px;font-weight:700;font-size:23px;color:var(--red)}
.contacts{position:absolute;left:31px;top:778px;display:flex;align-items:center;gap:11px;color:#fff}
.contact{display:flex;align-items:center;gap:5px;font-size:9.4px;font-weight:500;white-space:nowrap}
.contact-phone{font-size:17px;font-weight:700}
.contact svg{flex:none}
.social{display:flex;gap:5px}
.social-dot{width:14px;height:14px;border-radius:50%;background:var(--red)}
</style>
</head>
<body>
<main class="flyer">
  <div class="hero-photo" role="img" aria-label="Smiling senior couple embracing in a bright home"></div>

  <div class="brand"><span class="brand-mark"></span><span class="brand-name">Corvant Shield</span></div>

  <h1 class="headline">Our plans are based<br>on yours</h1>
  <p class="intro">Get the right Final Expense Insurance, Medicare Supplement Insurance or Mortgage Protection Insurance plan for your family's peace-of-mind!</p>

  <svg class="wave wave-top" viewBox="0 0 610 100" preserveAspectRatio="none" aria-hidden="true">
    <path d="M0,58 C150,40 300,60 430,92 C500,100 560,98 610,80 L610,100 L0,100Z" fill="var(--paper)"/>
    <path d="M0,14 C150,-4 300,18 420,58 C500,80 560,62 610,40 L610,54 C560,80 500,94 420,76 C300,42 150,10 0,20Z" fill="var(--black)"/>
    <path d="M0,30 C150,8 300,32 440,84 C520,100 570,90 610,74 L610,80 C560,98 500,100 430,92 C300,60 150,40 0,58Z" fill="var(--red)"/>
  </svg>

  <section class="col col-left">
    <h2 class="section-title">Final Expense Insurance</h2>
    <p class="justify">Final Expense Insurance is a type of permanent life insurance where the death benefit is used to cover (but not limited to) medical costs, funeral costs and other end-of-life expenses. It is a budget friendly option with a death benefit of up to $40k.</p>
    <h3 class="section-title" style="margin-top:12px">Benefits:</h3>
    <ul class="checks">
      <li>All plans we offer are state regulated</li>
      <li>Relatively low monthly premiums</li>
      <li>Premiums can never increase</li>
      <li class="justify">Your policy can never be cancelled as long as you pay your premium</li>
      <li>No medical exams</li>
      <li>Guaranteed Death Benefit</li>
      <li class="justify">Many policies we offer are Guaranteed Acceptance, "Day 1" coverage, have a child/grandchild rider and/or have an accelerated death benefit rider</li>
    </ul>
    <table class="price-table">
      <tr><th>Monthly premiums as low as</th><td>$10</td></tr>
      <tr><th>Death Benefits as high as</th><td>$40,000</td></tr>
    </table>
    <p class="disclaimer">Based on an insured that is a 65 year old, non-smoking female that has no medical conditions with death benefit of $2k</p>
  </section>

  <section class="col col-right">
    <h2 class="about-title">About Us</h2>
    <div class="block">
      <h3 class="sub-title">We Work for You</h3>
      <p>We have been helping clients in North Idaho/<br>Eastern Washington prepare for the unknown.<br><span class="also-title">We Also Specialize In:</span></p>
      <ul class="checks">
        <li>Medicare Supplement Insurance (MediGap)</li>
        <li>Annuities</li>
        <li>Final Expense</li>
      </ul>
      <p class="justify">We have access to the industry's top insurance carriers so you can get the right coverage that fits your budget.</p>
    </div>
    <div class="block">
      <h3 class="sub-title">Assessing Need</h3>
      <p class="justify">Unforeseen events and a lack of the right kind of insurance can spell trouble quickly. Contact us today, to set up a free assessment time. We will analyze your insurance needs and get you and your family the right coverage quickly at a budget friendly price.</p>
    </div>
    <div class="block">
      <h3 class="sub-title">Your Unique</h3>
      <p>Everyone has different insurance needs.<br>Find out how we can give you the peace of mind knowing your family wont have a financial burden if something were to happen to you.<br>and/or<br>Find out how we can help find the right plan to keep your medical costs manageable.</p>
    </div>
  </section>

  <svg class="wave wave-bottom" viewBox="0 0 610 130" preserveAspectRatio="none" aria-hidden="true">
    <path d="M0,20 C180,-6 350,60 510,82 C560,86 590,76 610,64 L610,130 L0,130Z" fill="var(--black)"/>
    <path d="M0,10 C180,-16 350,52 510,76 C560,82 590,70 610,56 L610,64 C590,76 560,86 510,82 C350,60 180,-6 0,20Z" fill="var(--red)"/>
  </svg>

  <p class="cta">Call us today!</p>
  <div class="contacts">
    <span class="contact contact-phone">
      <svg width="18" height="18" viewBox="0 0 24 24" aria-hidden="true"><path fill="var(--red)" d="M6.6 10.8a15.1 15.1 0 0 0 6.6 6.6l2.2-2.2c.3-.3.7-.4 1-.2 1.1.4 2.3.6 3.6.6.6 0 1 .4 1 1V20c0 .6-.4 1-1 1A17 17 0 0 1 3 4c0-.6.4-1 1-1h3.5c.6 0 1 .4 1 1 0 1.3.2 2.5.6 3.6.1.3 0 .7-.2 1z"/></svg>
      (208)555.0147
    </span>
    <span class="contact">
      <svg width="12" height="10" viewBox="0 0 24 18" aria-hidden="true"><path fill="var(--red)" d="M0 2l12 8 12-8v14H0z M1 0h22L12 7z"/></svg>
      tkelwer@corvantshield.com
    </span>
    <span class="contact">
      <svg width="12" height="12" viewBox="0 0 24 24" aria-hidden="true"><circle cx="12" cy="12" r="10" fill="none" stroke="var(--red)" stroke-width="2"/><path d="M2 12h20M12 2c3 3 3 17 0 20M12 2c-3 3-3 17 0 20" fill="none" stroke="var(--red)" stroke-width="1.6"/></svg>
      www.corvantshield.com
    </span>
    <span class="social">
      <span class="social-dot" role="img" aria-label="Social network profile link"></span>
      <span class="social-dot" role="img" aria-label="Second social network profile link"></span>
    </span>
  </div>
</main>
</body>
</html>
```